Direct to Consumer extended service contract business with a new disruptive business model needs a

We need a customized wordpress design for a company called 'Bright Harbor Assurance'.
We provide an innovative and unique service contract protection program direct to consumers. This program provides monthly coverage for all electronics purchased in the last 4 years and all electronics the consumer purchases in the future for a low monthly fee. The overall design should communicate a sense of legitimacy, ethics, and superior customer service and support (in an industry that has a huge PR issue to overcome).
Electronics is the first product group, other product groups with different price points to launch in the future..

Target Market(s)

All purchasers of electronic goods...all demographics

Industry/Entity Type

Electronics

Font styles to use
Sans Serif

Requirements
Must have
• Customer Testimonials
Industry News
Customer ratings
Blog posts
Call to action messaging
Like the functional elements and design of quillmesa.example (need to be better)
Nice to have
• Like to see video testimonials
Social network "whats trending related to electronics or service contract industry"
Easy way to register products for warranty

```html
<!DOCTYPE html>
<html lang="en">
<head>
<meta charset="utf-8">
<title>Bright Harbor Assurance</title>
<link rel="stylesheet" href="https://fonts.googleapis.com/css2?family=Signika:wght@300;400;600;700&family=Ubuntu:wght@400;500;700&family=Arimo:wght@400;700&display=swap">
<style>
:root{
  --topbar:#292929;
  --green:#2a8a58;
  --green-light:#4aa878;
  --green-text:#1f7a4a;
  --ink:#333333;
  --ink-soft:#555555;
  --welcome-bg:#e3e7e9;
  --features-bg:#464a50;
  --features-line:#6b7077;
  --panel-bg:#f0f0f0;
  --footer:#2c2c2c;
  --footer-low:#343434;
  --white:#ffffff;
}
*{margin:0;padding:0;box-sizing:border-box}
html,body{width:852px;height:1200px;overflow:hidden;background:var(--white)}
body{position:relative;font-family:"Arimo",Arial,sans-serif;color:var(--ink)}
.abs{position:absolute}

.topbar{left:0;top:0;width:852px;height:57px;background:var(--topbar)}
.brand{left:100px;top:14px;font-family:"Signika",sans-serif;font-weight:400;font-size:24px;color:var(--white)}
.social{right:100px;top:17px;display:flex;gap:4px}
.social span{width:22px;height:22px;border-radius:50%;background:#9a9a9a;display:block}

.navbar{left:0;top:57px;width:852px;height:43px;background:var(--green)}
.nav-home{left:98px;top:62px;width:58px;height:30px;background:var(--green-light);border-radius:3px}
.nav-link{top:72px;font-family:"Arimo",sans-serif;font-size:10.5px;color:var(--white);text-transform:uppercase}
.call-label{right:102px;top:60px;font-family:"Signika",sans-serif;font-size:14px;color:var(--white)}
.call-number{right:100px;top:74px;font-family:"Signika",sans-serif;font-size:20px;color:var(--white)}

.hero-title{left:100px;top:186px;font-family:"Signika",sans-serif;font-weight:300;font-size:31px;line-height:48px;color:#3a3a3a;text-transform:uppercase}
.hero-title strong{font-weight:600;color:var(--green-text)}
.device{top:134px;width:125px;height:248px;border-radius:16px}
.device-broken{left:461px;background:linear-gradient(160deg,#2c2c2c,#7d8a99 45%,#3a3f48)}
.device-fixed{left:629px;background:linear-gradient(160deg,#1e1e1e,#6a8bb0 45%,#2a2f38)}
.hero-arrow{left:590px;top:246px}

.welcome{left:0;top:418px;width:852px;height:300px;background:var(--welcome-bg)}
.welcome-photo{left:396px;top:418px;width:360px;height:300px;background:linear-gradient(180deg,#dfe4e7 0%,#c9a994 35%,#2b2e33 75%,#23262a 100%)}
.welcome-title{left:99px;top:448px;font-family:"Ubuntu",sans-serif;font-weight:700;font-size:22px;color:#2a2a2a;text-transform:uppercase}
.welcome-title span{font-weight:400}
.welcome-lead{left:99px;top:483px;width:320px;font-size:10.5px;line-height:12.5px;color:var(--green-text)}
.welcome-body{left:99px;top:517px;width:320px;font-size:9.8px;line-height:12.7px;color:var(--ink-soft)}
.btn-more{left:98px;top:596px;width:57px;height:30px;background:var(--green);border-radius:4px;color:var(--white);font-size:10.5px;line-height:30px;text-align:center}

.features{left:0;top:718px;width:852px;height:178px;background:var(--features-bg)}
.feature{top:746px;width:138px;text-align:center;color:var(--white)}
.feature h3{font-family:"Signika",sans-serif;font-weight:400;font-size:19px;line-height:24px;height:52px}
.feature hr{border:0;border-top:1px solid var(--features-line);margin:0 0 10px}
.feature p{font-family:"Ubuntu",sans-serif;font-size:8px;line-height:10px;color:#e4e4e4}
.feature svg{margin-top:16px}

.panel{left:0;top:896px;width:852px;height:206px;background:var(--panel-bg)}
.col-title{top:920px;font-family:"Ubuntu",sans-serif;font-weight:500;font-size:13px;color:#222}
.thumb{left:106px;width:48px;height:48px;background:linear-gradient(135deg,#f2d9c4,#c89a7a);border:2px solid var(--white);outline:1px solid #ddd}
.post-title{left:167px;font-family:"Ubuntu",sans-serif;font-weight:700;font-size:8.5px;color:#222}
.post-date{left:167px;font-family:"Ubuntu",sans-serif;font-weight:700;font-size:6.5px;color:#555;text-transform:uppercase}
.news-item{left:336px;font-family:"Ubuntu",sans-serif;font-weight:700;font-size:8px;color:#222;display:flex;align-items:center;gap:8px}
.news-body{left:336px;top:992px;width:240px;font-family:"Ubuntu",sans-serif;font-size:7.6px;line-height:11px;color:#666}
.news-rule{left:336px;top:1042px;width:240px;height:1px;background:#d8d8d8}
.quote{left:602px;top:947px;width:156px;height:79px;background:#dedede;padding:10px 8px;font-family:"Ubuntu",sans-serif;font-style:italic;font-size:8.3px;line-height:11.5px;color:#555}
.quote-tail{left:620px;top:1026px}
.avatar{left:607px;top:1039px;width:39px;height:39px;background:linear-gradient(135deg,#b9c7d3,#7a8896);border:2px solid var(--white)}
.author{left:656px;top:1044px;font-family:"Ubuntu",sans-serif;font-style:italic;font-size:9.5px;color:#2b4f8a}
.author-place{left:656px;top:1058px;font-family:"Ubuntu",sans-serif;font-size:7.5px;color:#444}

.footer{left:0;top:1102px;width:852px;height:50px;background:var(--footer)}
.footer-nav{left:0;top:1127px;width:852px;text-align:center;font-size:10px;color:#e8e8e8;word-spacing:2px}
.footer-nav i{font-style:normal;margin:0 14px}
.footer-low{left:0;top:1152px;width:852px;height:48px;background:var(--footer-low)}
.copyright{left:0;top:1164px;width:852px;text-align:center;font-size:8.5px;color:#8a8a8a}
</style>
</head>
<body>

<header>
  <div class="abs topbar"></div>
  <div class="abs brand">Bright Harbor Assurance</div>
  <div class="abs social" aria-label="Social links"><span></span><span></span><span></span><span></span></div>

  <nav>
    <div class="abs navbar"></div>
    <div class="abs nav-home"></div>
    <span class="abs nav-link" style="left:114px">Home</span>
    <span class="abs nav-link" style="left:175px">Reviews</span>
    <span class="abs nav-link" style="left:251px">Services</span>
    <span class="abs nav-link" style="left:330px">Blog</span>
    <span class="abs nav-link" style="left:389px">Contacts</span>
    <div class="abs call-label">Call us now</div>
    <div class="abs call-number">1 800 555 0142</div>
  </nav>
</header>

<section class="hero">
  <h1 class="abs hero-title">We give you innovative<br>services in the world<br>of <strong>electronic</strong></h1>
  <div class="abs device device-broken" role="img" aria-label="Smartphone with a cracked screen"></div>
  <svg class="abs hero-arrow" width="34" height="24" viewBox="0 0 34 24"><path d="M0 7h20V0l14 12-14 12v-7H0z" fill="#1db75f"/></svg>
  <div class="abs device device-fixed" role="img" aria-label="Same smartphone repaired with a clean screen"></div>
</section>

<section class="welcome-block">
  <div class="abs welcome"></div>
  <div class="abs welcome-photo" role="img" aria-label="Smiling businessman in a dark suit"></div>
  <h2 class="abs welcome-title">Welcome to our website<span>!</span></h2>
  <p class="abs welcome-lead">Lorem ipsum dolor sit amet conse ctetur adipisicing elit  sed do eiusmod tempor incidi</p>
  <p class="abs welcome-body">Phasellus porta. Fusce susct varius mi. Cum sociis natoque penabus et magnis dis parturient montes, nascetur ridiculus mus. Nulla dui. Fusce feugiat malesuada odio. Arenean lorem ipsum dolor sit amet conse ctetur adipisicing elit, sed do eiusmod tempor incidi dunt ut labore et dolore magna aliqua. Ut enim ad minim veniam…</p>
  <div class="abs btn-more">More</div>
</section>

<section class="features-block">
  <div class="abs features"></div>
  <div class="abs feature" style="left:123px"><h3>Monthly<br>Coverage</h3><hr><p>Et harum quidem rerum<br>harum quidem rerum facilis<br>consequatur out</p><svg width="20" height="20" viewBox="0 0 20 20"><circle cx="10" cy="10" r="10" fill="#2a2d31"/><path d="M8 6l4 4-4 4" stroke="#fff" stroke-width="2" fill="none"/></svg></div>
  <div class="abs feature" style="left:278px"><h3>Unique<br>Services</h3><hr><p>Et harum quidem rerum<br>harum quidem rerum facilis<br>consequatur out</p><svg width="20" height="20" viewBox="0 0 20 20"><circle cx="10" cy="10" r="10" fill="#2a2d31"/><path d="M8 6l4 4-4 4" stroke="#fff" stroke-width="2" fill="none"/></svg></div>
  <div class="abs feature" style="left:431px"><h3>Inspection &amp;<br>Testing</h3><hr><p>Et harum quidem rerum<br>harum quidem rerum facilis<br>consequatur out</p><svg width="20" height="20" viewBox="0 0 20 20"><circle cx="10" cy="10" r="10" fill="#2a2d31"/><path d="M8 6l4 4-4 4" stroke="#fff" stroke-width="2" fill="none"/></svg></div>
  <div class="abs feature" style="left:585px"><h3>New<br>Technologies</h3><hr><p>Et harum quidem rerum<br>harum quidem rerum facilis<br>consequatur out</p><svg width="20" height="20" viewBox="0 0 20 20"><circle cx="10" cy="10" r="10" fill="#2a2d31"/><path d="M8 6l4 4-4 4" stroke="#fff" stroke-width="2" fill="none"/></svg></div>
</section>

<section class="info-block">
  <div class="abs panel"></div>

  <h4 class="abs col-title" style="left:105px">Latest Posts</h4>
  <div class="abs thumb" style="top:952px" role="img" aria-label="Portrait thumbnail for a blog post"></div>
  <div class="abs post-title" style="top:961px">Dipisicing elit sed do eiusmod</div>
  <div class="abs post-date" style="top:975px">March 14, 2013</div>
  <div class="abs thumb" style="top:1010px" role="img" aria-label="Portrait thumbnail for a blog post"></div>
  <div class="abs post-title" style="top:1020px">Dipisicing elit sed do eiusmod</div>
  <div class="abs post-date" style="top:1034px">March 14, 2013</div>

  <h4 class="abs col-title" style="left:336px">News</h4>
  <div class="abs news-item" style="top:956px"><svg width="13" height="13" viewBox="0 0 13 13"><circle cx="6.5" cy="6.5" r="6.5" fill="#222"/><path d="M3.5 6.5h6" stroke="#fff" stroke-width="1.6"/></svg>Quisque nulla</div>
  <p class="abs news-body">Phasellus porta. Fusce susct varius mi. Cum sociis natoque penabus et magnis dis parturient montes, nascetur ridiculus mus. Nulla dui massa dolore sed lorem.</p>
  <div class="abs news-rule"></div>
  <div class="abs news-item" style="top:1054px"><svg width="13" height="13" viewBox="0 0 13 13"><circle cx="6.5" cy="6.5" r="6.5" fill="#222"/><path d="M3.5 6.5h6M6.5 3.5v6" stroke="#fff" stroke-width="1.6"/></svg>Vestibulum iaculis</div>

  <h4 class="abs col-title" style="left:607px">Testimonials</h4>
  <blockquote class="abs quote">"Aenean nonummy hendrerit mau Fusce suscipit varius mi sed. Cum penatibus et magnis dis parturient nascetur ridiculus mus. Nulla dui....</blockquote>
  <svg class="abs quote-tail" width="14" height="8" viewBox="0 0 14 8"><path d="M0 0h14L7 8z" fill="#dedede"/></svg>
  <div class="abs avatar" role="img" aria-label="Customer portrait"></div>
  <div class="abs author">Dana Whitfield</div>
  <div class="abs author-place">USA, Fairview</div>
</section>

<footer>
  <div class="abs footer"></div>
  <div class="abs footer-nav">Home<i>|</i>Reviews<i>|</i>Services<i>|</i>Blog<i>|</i>Contacts</div>
  <div class="abs footer-low"></div>
  <div class="abs copyright">Copyright 2014 www.brightharbor.example All Rights Reserved.</div>
</footer>

</body>
</html>
```